Bright Wave Labs

We need a professional letter head format for our company. Now we have a logo but need to desing a new logo also. I have uploaded our old logo. Use the color in the logo and design a new one.

Dear Designers , Need to mention "BWL" and please dont use our old LOGO. we need a new catchy one.

```html
<!DOCTYPE html>
<html lang="en">
<head>
<meta charset="utf-8">
<title>Bright Wave Labs — Letterhead</title>
<link rel="stylesheet" href="https://fonts.googleapis.com/css2?family=Open+Sans:wght@400;600&family=Lato:wght@400;700&display=swap">
<style>
  :root {
    --navy: #13294b;
    --green: #8fc43a;
    --ink: #4a4a4a;
    --ink-dark: #222222;
    --paper: #ffffff;
  }
  * { margin: 0; padding: 0; box-sizing: border-box; }
  html, body { width: 1040px; height: 1200px; overflow: hidden; background: var(--paper); }
  .letterhead {
    position: relative;
    width: 1040px; height: 1200px;
    font-family: "Open Sans", sans-serif;
    color: var(--ink);
  }
  .brand {
    position: absolute; top: 118px; left: 0; width: 100%;
    text-align: center;
  }
  .brand-name {
    display: inline-flex; align-items: center; gap: 12px;
    font-family: "Open Sans", sans-serif;
    font-weight: 600; font-size: 30px; letter-spacing: 0.5px;
    color: var(--navy);
  }
  .brand-square { width: 20px; height: 20px; background: var(--green); display: inline-block; }
  .letter {
    position: absolute; left: 97px; width: 840px;
    font-size: 16px; line-height: 27px;
  }
  .issue-date { top: 245px; }
  .recipient { top: 286px; line-height: 18px; font-style: normal; }
  .salutation { top: 382px; }
  .body-text { top: 437px; }
  .body-text p { text-align: justify; hyphens: auto; margin-bottom: 27px; }
  .closing { top: 840px; }
  .signatory { top: 920px; }
  .signatory-name { font-size: 19px; font-weight: 600; color: #3a3a3a; line-height: 26px; }
  .signatory-role { font-size: 16px; line-height: 24px; }
  .footer-square {
    position: absolute; left: 14px; top: 1140px; width: 24px; height: 24px;
    background: var(--navy);
  }
  .footer-address {
    position: absolute; top: 1124px; left: 110px; width: 820px;
    text-align: center;
    font-family: "Lato", sans-serif; font-size: 18px; color: var(--ink-dark);
  }
  .footer-bar {
    position: absolute; top: 1151px; left: 50px; width: 880px; height: 9px;
    background: var(--green);
  }
  .footer-contact {
    position: absolute; top: 1164px; left: 110px; width: 820px;
    display: flex; justify-content: center; gap: 24px;
    font-family: "Lato", sans-serif; font-size: 18px; color: var(--ink-dark);
  }
</style>
</head>
<body>
<main class="letterhead">
  <header class="brand">
    <span class="brand-name"><span class="brand-square"></span>Bright Wave Labs</span>
  </header>

  <p class="letter issue-date">Issuing Date: May 5, 2018</p>
  <address class="letter recipient">
    Name Of Employee Mr. XYZABC<br>
    Address of Employee<br>
    Address Line 2 etc..
  </address>
  <p class="letter salutation">Dear Mr.XYZABC</p>

  <section class="letter body-text">
    <p>Lorem Ipsum has been the industry's standard dummy text ever since the 1500s, when an unknown printer took a galley of type and scrambled it to make a type specimen book. It has survived not only five centuries, but also the leap into electronic typesetting, remaining essentially unchanged. It was popularised in the 1960s with the release of Lettrex sheets containing Lorem Ipsum passages, and more recently with desktop publishing software like PageForge Studio including versions of Lorem Ipsum.</p>
    <p>Lorem Ipsum is simply dummy text of the printing and typesetting industry. Lorem Ipsum has been the industry's standard dummy text ever since the 1500s, when an unknown printer took a galley of type and scrambled it to make a type specimen book.</p>
    <p>It has survived not only five centuries, but also the leap into electronic typesetting, remaining essentially unchanged. It was popularised in the 1960s with the release of Lettrex sheets containing Lorem IpsumIpsum passages.</p>
  </section>

  <p class="letter closing">Yours Sincerely</p>
  <div class="letter signatory">
    <p class="signatory-name">Daniel Harper</p>
    <p class="signatory-role">Managing Director</p>
  </div>

  <footer>
    <span class="footer-square"></span>
    <p class="footer-address">18, Harbour Row, 40210, Eastland</p>
    <div class="footer-bar"></div>
    <p class="footer-contact">
      <span>P: 044-555 018 272</span><span>|</span>
      <span>E: hello@brightwave.example</span><span>|</span>
      <span>www.brightwave.example</span>
    </p>
  </footer>
</main>
</body>
</html>
```